New Template, new corporate image Kelvoran 2022

New template designs for google slides or PowerPoint. Match to new corporate image. The new website www.kelvoran-mx.example Needs to match our new version. Technology and Artificial Intelligence elements to reflect our type of work.
We are adding old version of template and will send elements for the new corporate images.
Please consider our website as the main corporate image.
Our templates are being used on customer presentations, webminars, internal work only.
We have our main name of company Kelvoran. Kelvoran has to be in all the templates.
Secondary logo or branded service is: Vastrelim.

Target Market(s)

Industrial users. Asset managers. Corporate visitors and customers.

Industry/Entity Type

Automotive. Chemical. Food and Beverage. Manufacturing

Other font styles liked:
• GE INSPIRA. RALEWAY

Colors
0054AA
0677BA
7BADD7
CADEEF
E8F1F8

Requirements
Must have
• Match to our elements on the new image. Use Brain Icons. Chips icons to connect equipments with software and control. Innovation.
Nice to have
• Unique images, machine images. Connecting machines and data elements. Template version for google slides. Image for industrial software for control equipment and saving money to manufacturers. Segments: Automotive, Chemical, Food and Beverages, Mining and pharmaceutical, Energy Management
Should not have
• old elements. not to much images of medical devices. Do not seems like a hospital.

```html
<!DOCTYPE html>
<html lang="en">
<head>
<meta charset="utf-8">
<title>Kelvoran 2022 – Slide Template Part 2</title>
<link rel="stylesheet" href="https://fonts.googleapis.com/css2?family=Montserrat:wght@400;500;600;700;800;900&family=Archivo+Black&display=swap">
<style>
  :root {
    --blue-deep: #0054AA;
    --blue-mid: #0677BA;
    --blue-soft: #7BADD7;
    --blue-pale: #CADEEF;
    --blue-mist: #E8F1F8;
    --cyan: #00A3E8;
    --ink: #3a3a3a;
    --footer-dark: #2b2b2b;
    --canvas: #e6e6e6;
    --rule: #d6d6d6;
    --row-shade: #f1f1f1;
  }
  * { margin: 0; padding: 0; box-sizing: border-box; }
  html, body { width: 1200px; height: 1200px; overflow: hidden; background: var(--canvas); }
  body { position: relative; font-family: "Montserrat", sans-serif; color: var(--ink); }

  .slide { position: absolute; width: 544px; height: 306px; background: #fff; overflow: hidden; }
  .slide.right { width: 541px; }
  .col-left { left: 39px; }
  .col-right { left: 614px; }
  .row-1 { top: 38px; }
  .row-2 { top: 375px; }
  .row-3 { top: 711px; }

  .slide-title { position: absolute; left: 22px; top: 22px; font-size: 20.5px; font-weight: 700; color: var(--blue-deep); letter-spacing: .2px; }
  .abs { position: absolute; }

  .footer { position: absolute; left: 0; bottom: 0; width: 100%; height: 23px; }
  .footer svg { position: absolute; inset: 0; }
  .footer-copy { position: absolute; left: 22px; top: 7.5px; font-size: 5.6px; color: #fff; }
  .footer-copy .page-no { color: var(--cyan); margin-right: 3px; }
  .footer-brand { position: absolute; left: 467px; top: 7px; font-size: 7px; font-weight: 600; color: #fff; letter-spacing: .6px; text-transform: uppercase; }

  /* About */
  .hero { position: absolute; left: 0; top: 57px; width: 100%; height: 119px;
    background: linear-gradient(100deg, #0a1a3e 0%, #14306e 45%, #1f4f9a 70%, #1d7fa0 85%, #14305e 100%); }
  .hero-title { position: absolute; left: 22px; top: 34px; font-size: 15.5px; font-weight: 700; color: #fff; }
  .hero-text { position: absolute; left: 22px; top: 55px; width: 300px; font-size: 8.6px; line-height: 10.8px; color: #fff; }
  .about-col { position: absolute; top: 198px; width: 170px; text-align: center; }
  .about-col h3 { font-size: 12.2px; font-weight: 700; color: var(--blue-deep); }
  .about-col p { font-size: 8.2px; line-height: 9.6px; margin-top: 4px; }
  .vrule { position: absolute; width: 1px; background: var(--rule); }

  /* Team */
  .portrait { position: absolute; width: 88px; height: 88px; border-radius: 50%; border: 3px solid var(--blue-deep);
    background: linear-gradient(160deg, #c9d3cf 0%, #8a8f8c 55%, #5b6066 100%); box-shadow: inset 0 0 0 2px var(--cyan); }
  .member { position: absolute; top: 184px; width: 140px; }
  .member h3 { font-size: 11.4px; font-weight: 700; color: var(--blue-deep); }
  .member p { font-size: 9.4px; line-height: 10.9px; margin-top: 1px; }

  /* Charts */
  .chart-label { position: absolute; font-size: 10.5px; font-weight: 700; color: var(--blue-deep); text-align: center; }
  svg text { font-family: "Montserrat", sans-serif; }

  /* Services */
  .service { position: absolute; top: 65px; width: 122px; height: 160px; border: 1px solid var(--rule); text-align: center; }
  .service-icon { position: absolute; left: 35px; top: 19px; width: 52px; height: 52px; }
  .service h3 { position: absolute; left: 0; right: 0; top: 83px; font-size: 12.4px; font-weight: 700; color: var(--blue-deep); }
  .service p { position: absolute; left: 8px; right: 8px; top: 99px; font-size: 8.6px; line-height: 9.6px; }
  .services-note { position: absolute; left: 20px; right: 20px; top: 236px; text-align: center; font-size: 9.4px; line-height: 11px; }

  /* Table */
  .data-table { position: absolute; left: 22px; top: 61px; width: 499px; border-collapse: collapse; border-bottom: 1.5px solid var(--blue-deep); }
  .data-table th { background: var(--blue-deep); color: #fff; font-size: 11px; font-weight: 700; text-align: left; height: 31px; padding-left: 4px; }
  .data-table td { height: 32px; font-size: 10.4px; padding-left: 4px; }
  .data-table td:first-child { color: var(--blue-deep); font-weight: 700; }
  .data-table tbody tr:nth-child(even) td { background: var(--row-shade); }
  .data-table th:first-child, .data-table td:first-child { width: 66px; }

  /* Map */
  .map-area { position: absolute; left: 85px; top: 62px; width: 420px; height: 196px; border-radius: 40px 60px 30px 70px;
    background: radial-gradient(ellipse at 55% 45%, #c4c4c4 0%, #d3d3d3 60%, #e6e6e6 100%); }
  .pin { position: absolute; width: 20px; height: 20px; border-radius: 50%; background: linear-gradient(145deg, var(--blue-mid), var(--blue-deep));
    color: #fff; font-size: 6.6px; font-weight: 700; line-height: 20px; text-align: center; box-shadow: 0 0 0 2px #fff; }
  .map-note { position: absolute; width: 120px; }
  .map-note h4 { font-size: 7.6px; font-weight: 700; color: var(--blue-deep); }
  .map-note p { font-size: 5.6px; color: var(--ink); margin-top: 1px; }
  .map-note.align-end { text-align: right; }

  .part-label { position: absolute; left: 40px; top: 1040px; font-family: "Archivo Black", "Montserrat", sans-serif; font-size: 124px; line-height: 1; color: #000; letter-spacing: 2px; }
</style>
</head>
<body>

<!-- About Us -->
<section class="slide col-left row-1">
  <h2 class="slide-title">About Us</h2>
  <div class="hero" role="img" aria-label="Close-up photo of a glowing blue circuit board with a microchip">
    <div class="hero-title">Section Header</div>
    <p class="hero-text">Lorem ipsum dolor sit amet, consectetur adipiscing elit. Curabitur at fringilla velit. In ac sagittis nulla. Nulla quis erat et ligula aliquam sagittis in viverra mauris.</p>
  </div>
  <div class="about-col" style="left:10px"><h3>Section Header</h3><p>Lorem ipsum dolor sit amet,<br>consectetur at es adipiscing elit.<br>Curabitur fringilla velit.</p></div>
  <div class="vrule" style="left:187px; top:195px; height:64px"></div>
  <div class="about-col" style="left:193px"><h3>Section Header</h3><p>Lorem ipsum dolor sit amet,<br>consectetur at es adipiscing elit.<br>Curabitur fringilla velit.</p></div>
  <div class="vrule" style="left:370px; top:195px; height:64px"></div>
  <div class="about-col" style="left:375px"><h3>Section Header</h3><p>Lorem ipsum dolor sit amet,<br>consectetur at es adipiscing elit.<br>Curabitur fringilla velit.</p></div>
  <footer class="footer">
    <svg width="544" height="23"><rect width="544" height="23" fill="var(--blue-deep)"/><polygon points="433,0 449,0 464,23 448,23" fill="var(--cyan)"/><polygon points="449,0 544,0 544,23 464,23" fill="var(--footer-dark)"/></svg>
    <div class="footer-copy"><span class="page-no">7 |</span> Copyright © Kelvoran 2022</div>
    <div class="footer-brand">Kelvoran</div>
  </footer>
</section>

<!-- Meet Our Team -->
<section class="slide right col-right row-1">
  <h2 class="slide-title">Meet Our Team</h2>
  <div class="portrait" style="left:23px; top:78px" role="img" aria-label="Portrait photo of a team member"></div>
  <div class="portrait" style="left:200px; top:78px" role="img" aria-label="Portrait photo of a team member"></div>
  <div class="portrait" style="left:381px; top:78px" role="img" aria-label="Portrait photo of a team member"></div>
  <div class="vrule" style="left:173px; top:77px; height:174px"></div>
  <div class="vrule" style="left:353px; top:77px; height:174px"></div>
  <div class="member" style="left:22px"><h3>Enter Name Here</h3><p>Phasellus gravida mauris<br>a sapien elementum<br>malesuada. Vestibulum ut<br>urna eu dolor.</p></div>
  <div class="member" style="left:203px"><h3>Enter Name Here</h3><p>Phasellus gravida mauris<br>a sapien elementum<br>malesuada. Vestibulum ut<br>urna eu dolor.</p></div>
  <div class="member" style="left:385px"><h3>Enter Name Here</h3><p>Phasellus gravida mauris<br>a sapien elementum<br>malesuada. Vestibulum ut<br>urna eu dolor.</p></div>
  <footer class="footer">
    <svg width="541" height="23"><rect width="541" height="23" fill="var(--blue-deep)"/><polygon points="430,0 446,0 461,23 445,23" fill="var(--cyan)"/><polygon points="446,0 541,0 541,23 461,23" fill="var(--footer-dark)"/></svg>
    <div class="footer-copy"><span class="page-no">8 |</span> Copyright © Kelvoran 2022</div>
    <div class="footer-brand" style="left:464px">Kelvoran</div>
  </footer>
</section>

<!-- Chart with Content -->
<section class="slide col-left row-2">
  <h2 class="slide-title">Chart with Content</h2>
  <div class="chart-label" style="left:100px; top:67px; width:80px">Chart Title</div>
  <svg class="abs" style="left:0; top:0" width="544" height="283">
    <g stroke="#e2e2e2" stroke-width=".7">
      <line x1="37" y1="88" x2="253" y2="88"/><line x1="37" y1="111.5" x2="253" y2="111.5"/><line x1="37" y1="135" x2="253" y2="135"/>
      <line x1="37" y1="158.5" x2="253" y2="158.5"/><line x1="37" y1="182" x2="253" y2="182"/><line x1="37" y1="205.5" x2="253" y2="205.5"/>
      <line x1="37" y1="229" x2="253" y2="229"/>
    </g>
    <g font-size="6.8" fill="#666" text-anchor="middle">
      <text x="28" y="91">6</text><text x="28" y="114.5">5</text><text x="28" y="138">4</text><text x="28" y="161.5">3</text>
      <text x="28" y="185">2</text><text x="28" y="208.5">1</text><text x="28" y="232">0</text>
      <text x="63" y="241">Category 1</text><text x="117" y="241">Category 2</text><text x="171" y="241">Category 3</text><text x="225" y="241">Category 4</text>
    </g>
    <g>
      <rect x="46" y="127.9" width="9" height="101.1" fill="var(--blue-deep)"/><rect x="59" y="172.6" width="9" height="56.4" fill="var(--blue-mid)"/><rect x="72" y="182" width="9" height="47" fill="var(--blue-soft)"/>
      <rect x="100" y="170.3" width="9" height="58.7" fill="var(--blue-deep)"/><rect x="113" y="125.6" width="9" height="103.4" fill="var(--blue-mid)"/><rect x="126" y="182" width="9" height="47" fill="var(--blue-soft)"/>
      <rect x="154" y="146.8" width="9" height="82.2" fill="var(--blue-deep)"/><rect x="167" y="186.7" width="9" height="42.3" fill="var(--blue-mid)"/><rect x="180" y="158.5" width="9" height="70.5" fill="var(--blue-soft)"/>
      <rect x="208" y="123.3" width="9" height="105.7" fill="var(--blue-deep)"/><rect x="221" y="163.2" width="9" height="65.8" fill="var(--blue-mid)"/><rect x="234" y="111.5" width="9" height="117.5" fill="var(--blue-soft)"/>
    </g>
    <g font-size="7.8" fill="#666">
      <rect x="80" y="249" width="4" height="4" fill="var(--blue-deep)"/><text x="86" y="254">Series 1</text>
      <rect x="123" y="249" width="4" height="4" fill="var(--blue-mid)"/><text x="129" y="254">Series 2</text>
      <rect x="166" y="249" width="4" height="4" fill="var(--blue-soft)"/><text x="172" y="254">Series 3</text>
    </g>
    <line x1="284" y1="63" x2="284" y2="270" stroke="var(--rule)" stroke-width="1"/>
    <g transform="translate(405 163) rotate(-90)" fill="none" stroke-width="22">
      <circle r="65" stroke="var(--blue-deep)" stroke-dasharray="232.8 175.6"/>
      <circle r="65" stroke="var(--blue-mid)" stroke-dasharray="93.9 314.5" stroke-dashoffset="-232.8"/>
      <circle r="65" stroke="var(--blue-soft)" stroke-dasharray="44.9 363.5" stroke-dashoffset="-326.7"/>
      <circle r="65" stroke="var(--blue-pale)" stroke-dasharray="36.8 371.6" stroke-dashoffset="-371.6"/>
    </g>
    <g font-size="7.8" fill="#666">
      <rect x="326" y="249" width="3.5" height="3.5" fill="var(--blue-deep)"/><text x="331" y="254">1st Qtr</text>
      <rect x="365" y="249" width="3.5" height="3.5" fill="var(--blue-mid)"/><text x="371" y="254">2nd Qtr</text>
      <rect x="410" y="249" width="3.5" height="3.5" fill="var(--blue-soft)"/><text x="416" y="254">3rd Qtr</text>
      <rect x="453" y="249" width="3.5" height="3.5" fill="var(--blue-pale)"/><text x="459" y="254">4th Qtr</text>
    </g>
  </svg>
  <div class="chart-label" style="left:370px; top:67px; width:70px">Sales</div>
  <footer class="footer">
    <svg width="544" height="23"><rect width="544" height="23" fill="var(--blue-deep)"/><polygon points="433,0 449,0 464,23 448,23" fill="var(--cyan)"/><polygon points="449,0 544,0 544,23 464,23" fill="var(--footer-dark)"/></svg>
    <div class="footer-copy"><span class="page-no">9 |</span> Copyright © Kelvoran 2022</div>
    <div class="footer-brand">Kelvoran</div>
  </footer>
</section>

<!-- Services -->
<section class="slide right col-right row-2">
  <h2 class="slide-title">Services</h2>
  <div class="service" style="left:17px">
    <svg class="service-icon" viewBox="0 0 52 52"><defs><linearGradient id="ic" x1="0" y1="0" x2="1" y2="1"><stop offset="0" stop-color="#0a8fd6"/><stop offset="1" stop-color="var(--blue-deep)"/></linearGradient></defs>
      <circle cx="26" cy="26" r="26" fill="url(#ic)"/>
      <g stroke="#fff" stroke-width="1.8" fill="none"><circle cx="26" cy="26" r="4"/><circle cx="16" cy="16" r="3.5"/><circle cx="36" cy="16" r="3.5"/><circle cx="16" cy="36" r="3.5"/><circle cx="36" cy="36" r="3.5"/>
      <line x1="18.5" y1="18.5" x2="23" y2="23"/><line x1="33.5" y1="18.5" x2="29" y2="23"/><line x1="18.5" y1="33.5" x2="23" y2="29"/><line x1="33.5" y1="33.5" x2="29" y2="29"/></g></svg>
    <h3>Section Header</h3><p>Lorem ipsum dolor sit amet, consecteturat es adipiscing elit. Curabitur fringilla</p>
  </div>
  <div class="service" style="left:144px">
    <svg class="service-icon" viewBox="0 0 52 52"><circle cx="26" cy="26" r="26" fill="url(#ic)"/>
      <g stroke="#fff" stroke-width="1.8" fill="none"><rect x="16" y="17" width="20" height="15" rx="4"/><circle cx="22" cy="24" r="1.8"/><circle cx="30" cy="24" r="1.8"/><line x1="26" y1="17" x2="26" y2="13"/><circle cx="26" cy="12" r="1.5"/>
      <line x1="16" y1="24" x2="13" y2="24"/><line x1="36" y1="24" x2="39" y2="24"/><line x1="22" y1="32" x2="22" y2="39"/><line x1="26" y1="32" x2="26" y2="39"/><line x1="30" y1="32" x2="30" y2="39"/></g></svg>
    <h3>Section Header</h3><p>Lorem ipsum dolor sit amet, consecteturat es adipiscing elit. Curabitur fringilla</p>
  </div>
  <div class="service" style="left:271px">
    <svg class="service-icon" viewBox="0 0 52 52"><circle cx="26" cy="26" r="26" fill="url(#ic)"/>
      <polygon points="29,11 17,29 25,29 22,42 35,22 27,22 31,11" fill="none" stroke="#fff" stroke-width="1.8" stroke-linejoin="round"/></svg>
    <h3>Section Header</h3><p>Lorem ipsum dolor sit amet, consecteturat es adipiscing elit. Curabitur fringilla</p>
  </div>
  <div class="service" style="left:397px">
    <svg class="service-icon" viewBox="0 0 52 52"><circle cx="26" cy="26" r="26" fill="url(#ic)"/>
      <g stroke="#fff" stroke-width="1.8" fill="none"><rect x="19" y="12" width="14" height="5"/><path d="M19 17 L16 23 L16 40 L36 40 L36 23 L33 17 Z"/><line x1="16" y1="23" x2="36" y2="23"/></g>
      <circle cx="23" cy="31" r="3" fill="#fff"/></svg>
    <h3>Section Header</h3><p>Lorem ipsum dolor sit amet, consecteturat es adipiscing elit. Curabitur fringilla</p>
  </div>
  <p class="services-note">Lorem ipsum dolor sit amet, consectetur adipiscing elit. Curabitur at fringilla velit. In ac sagittis nulla.<br>Nulla quis erat et ligula aliquam sagittis in viverra mauris. Pellentesque pharetra hendrerit orci at.</p>
  <footer class="footer">
    <svg width="541" height="23"><rect width="541" height="23" fill="var(--blue-deep)"/><polygon points="430,0 446,0 461,23 445,23" fill="var(--cyan)"/><polygon points="446,0 541,0 541,23 461,23" fill="var(--footer-dark)"/></svg>
    <div class="footer-copy"><span class="page-no">10 |</span> Copyright © Kelvoran 2022</div>
    <div class="footer-brand" style="left:464px">Kelvoran</div>
  </footer>
</section>

<!-- Table Slides -->
<section class="slide col-left row-3">
  <h2 class="slide-title">Table Slides</h2>
  <table class="data-table">
    <thead><tr><th>Data</th><th>Header</th><th>Header</th><th>Header</th><th>Header</th><th>Header</th><th>Header</th><th>Header</th></tr></thead>
    <tbody>
      <tr><td>Value</td><td>00</td><td>00</td><td>00</td><td>00</td><td>00</td><td>00</td><td>00</td></tr>
      <tr><td>Value</td><td>00</td><td>00</td><td>00</td><td>00</td><td>00</td><td>00</td><td>00</td></tr>
      <tr><td>Value</td><td>00</td><td>00</td><td>00</td><td>00</td><td>00</td><td>00</td><td>00</td></tr>
      <tr><td>Value</td><td>00</td><td>00</td><td>00</td><td>00</td><td>00</td><td>00</td><td>00</td></tr>
      <tr><td>Value</td><td>00</td><td>00</td><td>00</td><td>00</td><td>00</td><td>00</td><td>00</td></tr>
    </tbody>
  </table>
  <footer class="footer">
    <svg width="544" height="23"><rect width="544" height="23" fill="var(--blue-deep)"/><polygon points="433,0 449,0 464,23 448,23" fill="var(--cyan)"/><polygon points="449,0 544,0 544,23 464,23" fill="var(--footer-dark)"/></svg>
    <div class="footer-copy"><span class="page-no">11 |</span> Copyright © Kelvoran 2022</div>
    <div class="footer-brand">Kelvoran</div>
  </footer>
</section>

<!-- Map Slide -->
<section class="slide right col-right row-3">
  <h2 class="slide-title">Map Slide</h2>
  <div class="map-area" role="img" aria-label="Grey world map showing the continents"></div>
  <div class="pin" style="left:132px; top:135px">01</div>
  <div class="pin" style="left:378px; top:108px">02</div>
  <div class="pin" style="left:261px; top:109px">03</div>
  <div class="pin" style="left:392px; top:218px">04</div>
  <div class="pin" style="left:253px; top:165px">05</div>
  <div class="pin" style="left:186px; top:197px">06</div>
  <div class="map-note align-end" style="left:1px; top:135px"><h4>Section Header</h4><p>Lorem ipsum dolor sit amet.</p></div>
  <div class="map-note" style="left:261px; top:85px"><h4>Section Header</h4><p>Lorem ipsum dolor sit amet.</p></div>
  <div class="map-note" style="left:408px; top:106px"><h4>Section Header</h4><p>Lorem ipsum dolor sit amet.</p></div>
  <div class="map-note" style="left:283px; top:163px"><h4>Section Header</h4><p>Lorem ipsum dolor sit amet.</p></div>
  <div class="map-note align-end" style="left:53px; top:196px"><h4>Section Header</h4><p>Lorem ipsum dolor sit amet.</p></div>
  <div class="map-note" style="left:422px; top:215px"><h4>Section Header</h4><p>Lorem ipsum dolor sit amet.</p></div>
  <footer class="footer">
    <svg width="541" height="23"><rect width="541" height="23" fill="var(--blue-deep)"/><polygon points="430,0 446,0 461,23 445,23" fill="var(--cyan)"/><polygon points="446,0 541,0 541,23 461,23" fill="var(--footer-dark)"/></svg>
    <div class="footer-copy"><span class="page-no">12 |</span> Copyright © Kelvoran 2022</div>
    <div class="footer-brand" style="left:464px">Kelvoran</div>
  </footer>
</section>

<div class="part-label">PART 2</div>

</body>
</html>
```